EXCITING DECK for Automotive dealers that shows how our Technology works.

General Concept
The deck should visually represent the Trade and Credit Lead Life Cycle program is a dynamic, interconnected journey, illustrating how leads are generated, nurtured, and converted. The focus should be on how your system flows seamlessly between credit and trade-in opportunities for consumers, with the goal of maximizing engagement and conversions.
Slide 1: Title Slide - Lead Life Cycle Program
• Visual Concept: A stylized cycle or wheel that represents the stages of the lead life cycle, with arrows connecting each stage.
• Headline: "Lead Life Cycle Program"
• Subhead line: "Credit Pre-Qualification and Trade-In Appraisal"
• Imagery: Modern, sleek graphics of vehicles, smartphones (for texting), email icons, and dollar signs for value.
Slide 2: Lead Generation Sources
• Visual Concept: A funnel with the top representing the different lead generation sources.
• Content:
o Top of Funnel (Leads Enter):
 Pre-Qualification Tool (Fast4Loan)- How it Works
 1. Converts Web Traffic into the highest quality lead on the market
 Vorqel Email/Mail Marketing – How it Works
 1. Delivers actionable leads from email marketing not Just OPENS AND CLICKS. Show the text demo. Audiences below
1. Past Sold Customers (Equity Targets)
2. Past Service Onlu Department Customers (Conquest Sales)
3. Unsold Leads (from previous interactions)
o Each source should have a distinct icon to represent it (e.g., envelope for email, a wrench for past service customers, etc.).
• Headline: "Multiple Lead Sources Feeding into the Program"
• Imagery: The funnel narrowing toward the next step with leads symbolized by icons flowing downward.
Slide 3: Credit Leads - Pre-Qualified Flow
• Visual Concept: A customer engaging with the Fast4Loan tool on their mobile, being pre-qualified, and then us sending a offer to appraise their trade.
• Flow Explanation:
o Customer pre-qualifies via Fast4Loan → Receives credit approval → Email and Mail Example to check trade-in value.
• Headline: "Pre-Qualified Leads: Offering Trade-In Appraisal"
• Imagery: A sequence that shows how a customer moves from pre-qualification to considering their trade-in value. To purchasing
Slide 4: Trade-In Leads - Valuation Flow
• Visual Concept: A customer who has received a trade-in valuation offer now being prompted to pre-qualify for financing.
• Flow Explanation:
o Customer texts for vehicle value → Receives trade-in appraisal → Offer to pre-qualify for financing appears link is at the bottom of the text response.
• Headline: "Trade-In Leads: Offering Credit Pre-Qualification"
• Imagery: A customer looking at their trade-in value on their phone and being shown an additional prompt to pre-qualify for a loan.
Slide 5: Cross-Offer Opportunities
• Visual Concept: A two-way street or cycle, illustrating the seamless transition between offering pre-qualification to trade-in customers and offering trade-in value to credit leads.
• Content:
o Two pathways:
1. Start as a Credit Lead → Offer Trade-In Valuation
2. Start as a Trade-In Lead → Offer Credit Pre-Qualification
o Headline: "Cross-Offer Opportunities for Maximum Engagement"
• Imagery: Arrows going in both directions, symbolizing the back-and-forth opportunities between credit and trade leads.
Digital Retargeting for Cross-Action Engagement
• Visual Concept: An omnichannel approach with a customer in the center, surrounded by email/Mail icons, Chatterbook, and Snapgrove logos. Arrows leading from each platform back to the customer, showing how these channels drive engagement.
• Content:
o Title: "Engage to Convert one lead type to get both with Email/Mail and Digital Retargeting"
o Explanation:
 Whether a lead starts as a Pre-Qualified Credit Lead or a Trade-In Valuation Lead, we use personalized Email/Mail Campaigns and Digital Retargeting Ads (Chatterbook & Snapgrove) to encourage them to take the next action.
 If they pre-qualify for credit, we retarget them with trade-in valuation offers.
 If they start with a trade-in valuation, we follow up with financing offers.
o Headline: "Leverage Email & Social Retargeting to Drive Cross-Action"
• Visuals:
o Icons of Email, Chatterbook, and Snapgrove: Showing the platforms through which you retarget leads.
o Customer Journey Map: Illustrating how leads who interacted once are guided to the next step (credit lead → trade-in offer, trade-in lead → pre-qualification).
o Arrows Flowing Between Channels: Showing how no matter where a lead starts, they are continually engaged through digital touchpoints until they complete both actions.
o Ad examples
• Call to Action: "Stay Top of Mind and Convert Leads into Multi-Action Customers"
This slide emphasizes how you’re leveraging both email/mail marketing and social media retargeting to move leads further along the customer journey, regardless of how they entered your funnel. The visuals should reinforce the idea of continuous engagement and omnipresent reminders for them to take action.
________________________________________
Slide 6: Lifecycle Representation
• Visual Concept: A circular diagram showing how leads can continuously move between credit and trade offers throughout their lifecycle.
• Content:
o Show how the lifecycle doesn’t end after one interaction, but can continue with follow-up offers.
o Headline: "Continuous Engagement Throughout the Lead Life Cycle"
• Imagery: Circular arrows or flowchart representing each stage looping back into the lifecycle, emphasizing that leads can be re-engaged.
Slide 7: Lead Conversion Goals
• Visual Concept: A progression from leads to successful transactions (e.g., a customer with keys to a new car). Showing that getting customers to take both of these actions delives a lead that is very committed to the process of buying.
• Content:
o End goal: Convert both credit and trade leads into sales.
o Show statistics or success metrics as optional data points.
o Headline: "Converting Leads into Sales"
• Imagery: A car dealership handing over keys, happy customers, and sold vehicles.
Slide 8: Next Steps / Call to Action
• Visual Concept: A final slide summarizing the key takeaways and next steps.
• Headline: "Maximize Lead Potential with Cross-Offer Opportunities"
• Imagery: A mix of credit leads, trade leads, and successful customer outcomes.
________________________________________These slides should be clean and modern, using simple but impactful visuals like arrows, icons, and flow diagrams to represent the journey. The key is to emphasize flow and interaction between credit and trade-in opportunities, showing the two-way cross-sell nature of your Lead Life Cycle Program.

I have attached a current deck so you can pull some basic product info and graphics into the new deck (PLEASE DONT JUST COPY THE OLD DECK). I have also included some of our email artwrok if you need it. If you want to look at our website go here www.plorvenadsgroup.example

Target Market(s)

Car Dealers

Industry/Entity Type

Automotive Marketing

Requirements
Must have
• PLEASE READ THE PROJECT DESCRIPTION
Nice to have
Should not have
• PLEASE dont just copy the deck i uploaded. I am looking for a differnt take.

```html
<!DOCTYPE html>
<html lang="en">
<head>
<meta charset="utf-8">
<title>Lead Life Cycle Program</title>
<link rel="stylesheet" href="https://fonts.googleapis.com/css2?family=Lexend:wght@400;500&family=Lato:wght@400;700&display=swap">
<style>
:root{
  --red:#e0081c;
  --dark:#3a3a3c;
  --page:#e6e6e6;
  --white:#ffffff;
  --grey:#bdbdbd;
  --text:#2b2b2b;
  --muted:#4a4a4a;
}
*{box-sizing:border-box;margin:0;padding:0}
html,body{width:1200px;height:4035px;overflow:hidden;background:var(--page)}
body{position:relative;font-family:'Lato',sans-serif;color:var(--text)}
.slide{position:absolute;left:50px;width:1097px;height:617px;background:var(--white);box-shadow:0 1px 3px rgba(0,0,0,.12);overflow:hidden}
.abs{position:absolute}
.header-band{position:absolute;left:0;top:0;width:694px;height:66px}
.header-title{position:absolute;left:53px;top:0;height:66px;display:flex;align-items:center;font-family:'Lexend',sans-serif;font-weight:400;font-size:23px;line-height:31px;letter-spacing:1.2px;color:var(--white);text-transform:uppercase}
.brand{position:absolute;right:57px;top:16px;display:flex;align-items:center;gap:8px;font-family:'Lato',sans-serif;font-weight:700;font-size:15px;letter-spacing:2px;color:var(--dark);text-transform:uppercase}
.brand-mark{width:12px;height:12px;background:var(--red)}
.footer-date{position:absolute;left:53px;top:584px;font-size:12px;font-weight:700;color:var(--red)}
.footer-page{position:absolute;right:57px;top:584px;font-size:12px;font-weight:700;color:var(--text)}
.photo{position:absolute}
.photo-line{position:absolute;height:5px;background:var(--red)}
/* slide 1 */
.cover-brand{position:absolute;left:0;width:100%;top:60px;text-align:center;font-weight:700;font-size:22px;letter-spacing:4px;color:var(--dark);text-transform:uppercase}
.cover-brand span{display:inline-block;width:14px;height:14px;background:var(--red);margin-right:10px;vertical-align:middle}
.cover-title{position:absolute;left:0;width:100%;top:150px;text-align:center;font-family:'Lexend',sans-serif;font-weight:500;font-size:38px;letter-spacing:1.5px;color:var(--red);text-transform:uppercase}
.cover-sub{position:absolute;left:0;width:100%;top:219px;text-align:center;font-size:20px;color:var(--text)}
.stage{position:absolute;top:278px;width:188px;height:188px;border-radius:50%;border:20px solid var(--red);display:flex;flex-direction:column;align-items:center;justify-content:center;gap:6px}
.stage.dark{border-color:var(--dark)}
.stage-label{font-family:'Lexend',sans-serif;font-size:17px;line-height:22px;text-align:center;color:var(--dark);text-transform:uppercase}
.stage-note{position:absolute;top:480px;width:230px;text-align:center;font-size:12.5px;line-height:22px;color:var(--text)}
.stage-arrow{position:absolute;top:358px}
/* slide 2 */
.funnel-text{position:absolute;text-align:center;color:var(--white)}
/* timelines */
.step-line{position:absolute;width:3px;background:var(--grey)}
.step-dot{position:absolute;width:84px;height:84px;border-radius:50%;display:flex;align-items:center;justify-content:center}
.step-dot.red{background:var(--red)}
.step-dot.dark{background:var(--dark)}
.step-text{position:absolute;font-size:19px;line-height:32px;font-weight:700;color:var(--text)}
/* gauges */
.gauge{position:absolute;width:150px;height:150px}
.gauge-num{position:absolute;left:0;top:0;width:150px;height:150px;display:flex;align-items:center;justify-content:center;font-size:44px;font-weight:700;color:var(--text)}
.gauge-label{position:absolute;width:200px;text-align:center;font-size:19px;font-weight:700;color:var(--text)}
/* slide 6 */
.body-copy{position:absolute;left:55px;width:390px;font-size:16px;line-height:32px;color:var(--muted)}
.body-copy p+p{margin-top:32px}
</style>
</head>
<body>

<!-- Slide 1 -->
<section class="slide" style="top:44px">
  <svg class="abs" style="left:0;top:0" width="1097" height="130">
    <polygon points="0,0 219,0 0,124" fill="#3a3a3c"/>
    <polygon points="874,0 1097,0 1097,124" fill="#e0081c"/>
  </svg>
  <div class="cover-brand"><span></span>Norvale Marketing</div>
  <h1 class="cover-title">Lead Life Cycle Program</h1>
  <p class="cover-sub">Credit Pre-Qualification and Trade-In Appraisal</p>

  <div class="stage" style="left:64px">
    <svg width="50" height="36" viewBox="0 0 50 36"><path d="M8 14 L13 4 H37 L42 14 H46 V28 H40 V33 H33 V28 H17 V33 H10 V28 H4 V14 Z" fill="#3a3a3c"/><rect x="15" y="8" width="20" height="6" fill="#fff"/><circle cx="12" cy="20" r="3" fill="#fff"/><circle cx="38" cy="20" r="3" fill="#fff"/></svg>
    <div class="stage-label">Vehicles</div>
  </div>
  <div class="stage dark" style="left:323px">
    <svg width="30" height="50" viewBox="0 0 30 50"><rect x="3" y="2" width="24" height="46" rx="4" fill="none" stroke="#3a3a3c" stroke-width="4"/><circle cx="15" cy="41" r="2.5" fill="#3a3a3c"/></svg>
    <div class="stage-label">Smart<br>Phones</div>
  </div>
  <div class="stage" style="left:582px">
    <svg width="50" height="36" viewBox="0 0 50 36"><rect x="2" y="2" width="46" height="32" rx="3" fill="#3a3a3c"/><path d="M4 5 L25 20 L46 5" fill="none" stroke="#fff" stroke-width="3"/></svg>
    <div class="stage-label">Email</div>
  </div>
  <div class="stage dark" style="left:840px">
    <svg width="30" height="46" viewBox="0 0 30 46"><text x="15" y="38" text-anchor="middle" font-family="Lato, sans-serif" font-weight="700" font-size="44" fill="#3a3a3c">$</text></svg>
    <div class="stage-label">Dollar<br>Sign</div>
  </div>

  <svg class="stage-arrow" style="left:273px" width="34" height="28" viewBox="0 0 34 28"><path d="M2 14 H30 M19 3 L30 14 L19 25" fill="none" stroke="#2b2b2b" stroke-width="4"/></svg>
  <svg class="stage-arrow" style="left:532px" width="34" height="28" viewBox="0 0 34 28"><path d="M2 14 H30 M19 3 L30 14 L19 25" fill="none" stroke="#2b2b2b" stroke-width="4"/></svg>
  <svg class="stage-arrow" style="left:791px" width="34" height="28" viewBox="0 0 34 28"><path d="M2 14 H30 M19 3 L30 14 L19 25" fill="none" stroke="#2b2b2b" stroke-width="4"/></svg>

  <p class="stage-note" style="left:43px">We Offer Mobile Marketing<br>Solutions That Connect Advertisers<br>With More Interested Prospects</p>
  <p class="stage-note" style="left:302px">We Offer Mobile Marketing<br>Solutions That Connect Advertisers<br>With More Interested Prospects</p>
  <p class="stage-note" style="left:561px">We Offer Mobile Marketing<br>Solutions That Connect Advertisers<br>With More Interested Prospects</p>
  <p class="stage-note" style="left:819px">We Offer Mobile Marketing<br>Solutions That Connect Advertisers<br>With More Interested Prospects</p>

  <div class="footer-date">05 Oct 2024</div>
  <div class="footer-page">Page no: 01</div>
</section>

<!-- Slide 2 -->
<section class="slide" style="top:710px">
  <svg class="header-band" viewBox="0 0 694 66"><polygon points="0,0 694,0 660,66 0,66" fill="#e0081c"/></svg>
  <h2 class="header-title">Lead Generation Sources</h2>
  <div class="brand"><span class="brand-mark"></span>Norvale Marketing</div>

  <svg class="abs" style="left:0;top:0" width="1097" height="617">
    <polygon points="227,121 838,121 752,280 318,280" fill="#3a3a3c"/>
    <polygon points="322,290 747,290 686,415 372,415" fill="#e0081c"/>
    <rect x="395" y="426" width="277" height="125" fill="#3a3a3c"/>
    <path d="M421 482 V510 M410 500 L421 512 L432 500" fill="none" stroke="#fff" stroke-width="6"/>
    <path d="M642 482 V510 M631 500 L642 512 L653 500" fill="none" stroke="#fff" stroke-width="6"/>
  </svg>
  <div class="funnel-text" style="left:280px;width:540px;top:161px;font-size:15px;line-height:34px">
    <strong style="font-weight:700">Pre-Qualification Tool (Fast4Loan)- How it Works</strong><br>
    <span style="font-size:12.5px">1. Converts Web Traffic into the highest quality lead on the market</span>
  </div>
  <div class="funnel-text" style="left:340px;width:400px;top:294px;font-size:12.5px;line-height:28.5px">
    <strong style="font-size:15px">Vorqel Email/Mail Marketing – How it Works</strong><br>
    1. Delivers actionable leads from email marketing not<br>Just OPENS AND CLICKS. Show the text demo.<br>Audiences below
  </div>
  <div class="funnel-text" style="left:440px;width:190px;top:444px;font-size:15px;line-height:29px">Multiple Lead Sources Feeding into the Program</div>

  <div class="footer-date">05 Oct 2024</div>
  <div class="footer-page">Page no: 02</div>
</section>

<!-- Slide 3 -->
<section class="slide" style="top:1372px">
  <svg class="header-band" viewBox="0 0 694 66"><polygon points="0,0 694,0 660,66 0,66" fill="#3a3a3c"/></svg>
  <h2 class="header-title">Pre-Qualified Leads: Offering Trade-In<br>Appraisal</h2>
  <div class="brand"><span class="brand-mark"></span>Norvale Marketing</div>

  <div class="photo" role="img" aria-label="Customer holding a smartphone showing the Fast4Trade app in a warm bedroom" style="left:55px;top:121px;width:527px;height:402px;background:linear-gradient(135deg,#2a1a12 0%,#8a6248 45%,#d8c2ad 75%,#f1e6da 100%)"></div>
  <div class="photo-line" style="left:55px;top:522px;width:527px"></div>

  <div class="step-line" style="left:716px;top:190px;height:290px"></div>
  <div class="step-dot red" style="left:675px;top:113px">
    <svg width="40" height="40" viewBox="0 0 40 40" fill="none" stroke="#fff" stroke-width="2"><circle cx="17" cy="11" r="6"/><path d="M5 36 V28 Q5 20 17 20 Q25 20 27 24"/><circle cx="29" cy="29" r="5"/><path d="M26 33 L25 39 L29 37 L33 39 L32 33"/></svg>
  </div>
  <div class="step-dot dark" style="left:675px;top:277px">
    <svg width="40" height="40" viewBox="0 0 40 40" fill="none" stroke="#fff" stroke-width="2"><rect x="4" y="8" width="30" height="24" rx="3"/><path d="M4 15 H22 M9 25 H15 M28 4 V15 M24 11 L28 15 L32 11"/></svg>
  </div>
  <div class="step-dot red" style="left:675px;top:444px">
    <svg width="40" height="40" viewBox="0 0 40 40" fill="none" stroke="#fff" stroke-width="2"><circle cx="19" cy="21" r="14"/><circle cx="19" cy="21" r="9"/><circle cx="19" cy="21" r="4"/><path d="M19 21 L33 7 M29 5 L33 7 L35 11"/></svg>
  </div>
  <p class="step-text" style="left:783px;top:123px">Pre-qualifies<br>via Fast4Loan</p>
  <p class="step-text" style="left:783px;top:287px">Receives credit<br>approval</p>
  <p class="step-text" style="left:783px;top:450px">Email and Mail Example to<br>check trade-in value</p>

  <div class="footer-date">05 Oct 2024</div>
  <div class="footer-page">Page no: 03</div>
</section>

<!-- Slide 4 -->
<section class="slide" style="top:2030px">
  <svg class="header-band" viewBox="0 0 694 66"><polygon points="0,0 694,0 660,66 0,66" fill="#e0081c"/></svg>
  <h2 class="header-title">Trade-In Leads: Offering Credit<br>Pre-Qualification</h2>
  <div class="brand"><span class="brand-mark"></span>Norvale Marketing</div>

  <div class="step-line" style="left:96px;top:195px;height:290px"></div>
  <div class="step-dot red" style="left:55px;top:118px">
    <svg width="40" height="40" viewBox="0 0 40 40" fill="none" stroke="#fff" stroke-width="2"><circle cx="17" cy="11" r="6"/><path d="M5 36 V28 Q5 20 17 20 Q25 20 27 24"/><circle cx="29" cy="29" r="5"/><path d="M26 33 L25 39 L29 37 L33 39 L32 33"/></svg>
  </div>
  <div class="step-dot dark" style="left:55px;top:281px">
    <svg width="40" height="40" viewBox="0 0 40 40" fill="none" stroke="#fff" stroke-width="2"><rect x="4" y="8" width="30" height="24" rx="3"/><path d="M4 15 H22 M9 25 H15 M28 4 V15 M24 11 L28 15 L32 11"/></svg>
  </div>
  <div class="step-dot red" style="left:55px;top:446px">
    <svg width="40" height="40" viewBox="0 0 40 40" fill="none" stroke="#fff" stroke-width="2"><circle cx="19" cy="21" r="14"/><circle cx="19" cy="21" r="9"/><circle cx="19" cy="21" r="4"/><path d="M19 21 L33 7 M29 5 L33 7 L35 11"/></svg>
  </div>
  <p class="step-text" style="left:161px;top:128px">Customer texts for vehicle<br>value</p>
  <p class="step-text" style="left:161px;top:291px">Receives credit<br>approval</p>
  <p class="step-text" style="left:162px;top:436px">Offer to pre-qualify for financing<br>link is at the bottom of the text<br>response</p>

  <div class="photo-line" style="left:512px;top:120px;width:528px"></div>
  <div class="photo" role="img" aria-label="Smiling customer in a shopping mall reading a text message on her phone" style="left:512px;top:125px;width:528px;height:396px;background:linear-gradient(120deg,#e9e2d8 0%,#c9a98c 40%,#8a5a3e 65%,#cfd6dc 100%)"></div>
  <svg class="abs" style="left:598px;top:224px" width="78" height="70" viewBox="0 0 78 70"><rect x="0" y="0" width="78" height="54" rx="6" fill="#e0081c"/><polygon points="14,54 30,54 14,70" fill="#e0081c"/><rect x="14" y="18" width="42" height="5" fill="#fff"/><rect x="14" y="30" width="28" height="5" fill="#fff"/></svg>
  <div class="photo-line" style="left:512px;top:521px;width:528px"></div>

  <div class="footer-date">05 Oct 2024</div>
  <div class="footer-page">Page no: 04</div>
</section>

<!-- Slide 5 -->
<section class="slide" style="top:2691px">
  <svg class="header-band" viewBox="0 0 694 66"><polygon points="0,0 694,0 660,66 0,66" fill="#3a3a3c"/></svg>
  <h2 class="header-title">Converting Leads into Sales</h2>
  <div class="brand"><span class="brand-mark"></span>Norvale Marketing</div>

  <div class="photo" role="img" aria-label="Happy customer in the driver's seat receiving the keys to her new car" style="left:55px;top:122px;width:547px;height:402px;background:linear-gradient(120deg,#1c1c1e 0%,#3b3633 35%,#9a7a64 60%,#e5dcd4 100%)"></div>
  <div class="photo-line" style="left:55px;top:523px;width:547px"></div>

  <svg class="gauge" style="left:671px;top:121px" viewBox="0 0 150 150"><circle cx="75" cy="75" r="64" fill="none" stroke="#bdbdbd" stroke-width="9"/><circle cx="75" cy="75" r="64" fill="none" stroke="#e0081c" stroke-width="9" stroke-dasharray="300 402" transform="rotate(-90 75 75)"/></svg>
  <div class="gauge-num" style="left:671px;top:121px">35</div>
  <svg class="gauge" style="left:895px;top:121px" viewBox="0 0 150 150"><circle cx="75" cy="75" r="64" fill="none" stroke="#bdbdbd" stroke-width="9"/><circle cx="75" cy="75" r="64" fill="none" stroke="#e0081c" stroke-width="9" stroke-dasharray="320 402" transform="rotate(-90 75 75)"/></svg>
  <div class="gauge-num" style="left:895px;top:121px">72</div>
  <svg class="gauge" style="left:671px;top:336px" viewBox="0 0 150 150"><circle cx="75" cy="75" r="64" fill="none" stroke="#bdbdbd" stroke-width="9"/><circle cx="75" cy="75" r="64" fill="none" stroke="#e0081c" stroke-width="9" stroke-dasharray="330 402" transform="rotate(-90 75 75)"/></svg>
  <div class="gauge-num" style="left:671px;top:336px">95</div>
  <svg class="gauge" style="left:895px;top:340px" viewBox="0 0 150 150"><circle cx="75" cy="75" r="64" fill="none" stroke="#bdbdbd" stroke-width="9"/><circle cx="75" cy="75" r="64" fill="none" stroke="#e0081c" stroke-width="9" stroke-dasharray="300 402" transform="rotate(-90 75 75)"/></svg>
  <div class="gauge-num" style="left:895px;top:340px">14</div>

  <p class="gauge-label" style="left:646px;top:288px">Lorem ipsum</p>
  <p class="gauge-label" style="left:870px;top:288px">Lorem ipsum</p>
  <p class="gauge-label" style="left:646px;top:503px">Lorem ipsum</p>
  <p class="gauge-label" style="left:870px;top:507px">Lorem ipsum</p>

  <div class="footer-date">05 Oct 2024</div>
  <div class="footer-page">Page no: 05</div>
</section>

<!-- Slide 6 -->
<section class="slide" style="top:3349px">
  <svg class="header-band" viewBox="0 0 694 66"><polygon points="0,0 694,0 660,66 0,66" fill="#e0081c"/></svg>
  <h2 class="header-title">Maximize Lead Potential with<br>Cross-Offer Opportunities</h2>
  <div class="brand"><span class="brand-mark"></span>Norvale Marketing</div>

  <div class="body-copy" style="top:129px">
    <p>Marketing is about people. The purpose of any marketing plan is to identify the best prospects, deliver compelling messaging,<br>and then make the vehicle for the responses user-friendly.</p>
    <p>A successful marketing campaign is an equitable exchange of valuable information between a potential customer and a business.Our specialty at Norvale Marketing is making that connection.Every single piece of direct mail that is being sent in this country today needs to have text engagement.</p>
  </div>

  <div class="photo-line" style="left:512px;top:120px;width:528px"></div>
  <div class="photo" role="img" aria-label="Two smiling customers on a sofa looking at their smartphones" style="left:512px;top:125px;width:528px;height:399px;background:linear-gradient(110deg,#2f3440 0%,#4a4f5c 40%,#8d8f99 65%,#c9cbd3 100%)"></div>
  <div class="photo-line" style="left:512px;top:524px;width:528px"></div>

  <div class="footer-date">05 Oct 2024</div>
  <div class="footer-page">Page no: 06</div>
</section>

</body>
</html>
```